Social Media Graphics - Oakline Push REVISED

Create 6-7 individual social media graphics (square size) to encourage folks to join our online course called:

The Harvest Ledger Circle
How to Launch a Multi-Million Business From Scratch
Sign Up Today!

IMPORTANT: Make the largest and most prominent text on the graphic be: How to Launch a Multi-Million Business From Scratch

For the color scheme of the graphics, let's try a blue color palette; make sure the graphics appeal to both men and women

Make sure each graphic contains 1 of the 3 pics attached (crop pic as needed); and make sure one of the graphics is all TEXT only.

Target Market(s)

men and women looking to start a business

Industry/Entity Type

Entrepreneurship

Colors
0054AA
0677BA
7BADD7
CADEEF
E8F1F8

Requirements
Must have
• All the text and use the 3 pics provided; one graphic can be all text; Simple, modern design that's easy to read

```html
<!DOCTYPE html>
<html lang="en">
<head>
<meta charset="UTF-8">
<title>The Harvest Ledger Circle – Social Graphic</title>
<link rel="stylesheet" href="https://fonts.googleapis.com/css2?family=League+Spartan:wght@600;700;800&display=swap">
<style>
  :root {
    --navy-deep: #050a2e;
    --navy: #0b1f6e;
    --sky-panel: #0879bd;
    --royal: #004fb0;
    --cream: #fff5d6;
    --white: #ffffff;
    --mist: #e8f1f8;
    --photo-warm: #8a6a55;
    --photo-cool: #3f5f95;
  }
  * { margin: 0; padding: 0; box-sizing: border-box; }
  html, body { width: 1200px; height: 1200px; overflow: hidden; background: var(--navy-deep); }
  .graphic {
    position: relative;
    width: 1200px;
    height: 1200px;
    overflow: hidden;
    font-family: "League Spartan", "Montserrat", sans-serif;
    background: radial-gradient(ellipse at 20% 75%, var(--navy) 0%, #08155a 40%, var(--navy-deep) 100%);
  }
  .backdrop { position: absolute; inset: 0; }
  .course-name {
    position: absolute;
    top: 143px;
    left: 0;
    width: 1200px;
    text-align: center;
    color: var(--cream);
    font-weight: 700;
    font-size: 50px;
    letter-spacing: 2px;
    line-height: 1;
    text-transform: uppercase;
  }
  .headline {
    position: absolute;
    left: 0;
    width: 1200px;
    text-align: center;
    color: var(--white);
    font-weight: 700;
    text-transform: uppercase;
    line-height: 1;
  }
  .headline span { position: absolute; left: 0; width: 100%; white-space: nowrap; }
  .headline .l1 { top: 236px; font-size: 79px; letter-spacing: 1px; }
  .headline .l2 { top: 328px; font-size: 112px; letter-spacing: 1px; }
  .headline .l3 { top: 442px; font-size: 106px; letter-spacing: 1px; }
  .headline .l4 { top: 550px; font-size: 113px; letter-spacing: 1px; }
  .cta {
    position: absolute;
    left: 870px;
    top: 965px;
    width: 270px;
    text-align: center;
    color: var(--mist);
    font-weight: 700;
    font-size: 60px;
    line-height: 1.13;
    text-transform: uppercase;
    letter-spacing: 1px;
  }
  .photo {
    position: absolute;
    border-radius: 140px 140px 0 0;
  }
  .photo--host-left {
    left: 0; top: 705px; width: 295px; height: 495px;
    background: linear-gradient(180deg, var(--photo-warm) 0%, #4a5f93 55%, var(--photo-cool) 100%);
  }
  .photo--host-right {
    left: 335px; top: 714px; width: 500px; height: 486px;
    background: linear-gradient(180deg, var(--photo-warm) 0%, #7d7a78 45%, #9c9a97 100%);
  }
</style>
</head>
<body>
  <main class="graphic">
    <svg class="backdrop" width="1200" height="1200" viewBox="0 0 1200 1200" aria-hidden="true">
      <polygon class="sky-panel" points="0,0 1200,0 1200,472 597,1073 0,484" fill="var(--sky-panel)"/>
      <polygon class="top-notch" points="503,0 745,0 626,119" fill="var(--royal)"/>
    </svg>

    <p class="course-name">The Harvest Ledger Circle</p>

    <h1 class="headline">
      <span class="l1">How to Launch</span>
      <span class="l2">A Multi-Million</span>
      <span class="l3">Business From</span>
      <span class="l4">Scratch</span>
    </h1>

    <div class="photo photo--host-left" role="img" aria-label="Photo of a smiling woman in a blue blazer, one of the course hosts"></div>
    <div class="photo photo--host-right" role="img" aria-label="Photo of a smiling man in a grey blazer speaking into a microphone on stage"></div>

    <p class="cta">Sign Up<br>Today</p>
  </main>
</body>
</html>
```